TalkHarbor - Language Coaching Services

Sleek, innovative, trendy design for Language Coaching business.

TalkHarbor is a new UK based company that provides Language Coaching services. We offer highly personalized on-line and face to face language courses. We also impart learning techniques workshops based on the latest neuroscience research for second-language acquisition.

Target Market(s)

See attached info

Industry/Entity Type

Consulting

Contact Information for Business Card

TalkHarbor
DaniaKV@talkharbor.co.uk
TalkHarbor.co.uk
London, UK

Font styles to use
Sans Serif

```html
<!DOCTYPE html>
<html lang="en">
<head>
<meta charset="utf-8">
<title>TalkHarbor – Business Card</title>
<link rel="stylesheet" href="https://fonts.googleapis.com/css2?family=Montserrat:wght@400;600;700&family=Roboto:wght@400&display=swap">
<style>
  :root {
    --stage: #2b2b2d;
    --card-dark: #1d1e20;
    --card-light: #ffffff;
    --brand-blue: #0a7ab8;
    --brand-blue-deep: #0670a8;
    --ink: #3a3a3a;
    --ink-soft: #8a8a8a;
  }
  * { box-sizing: border-box; margin: 0; padding: 0; }
  html, body {
    width: 1200px; height: 960px; overflow: hidden;
    background: var(--stage);
  }
  .canvas {
    position: relative; width: 1200px; height: 960px;
  }
  .card {
    position: absolute; left: 220px; width: 760px; height: 434px;
    overflow: hidden;
    box-shadow: 0 10px 30px rgba(0,0,0,.45);
  }
  .card--back { top: 30px; background: var(--card-dark); }
  .card--front { top: 496px; background: var(--card-light); }

  /* back */
  .back-brand {
    position: absolute; inset: 0;
    display: flex; align-items: center; justify-content: center; gap: 22px;
  }
  .brand-dot {
    width: 74px; height: 74px; border-radius: 50%;
    border: 6px solid var(--brand-blue);
  }
  .wordmark {
    font-family: "Montserrat", sans-serif; font-weight: 600;
    color: var(--brand-blue); letter-spacing: 2px; text-transform: uppercase;
    white-space: nowrap;
  }
  .back-brand .wordmark { font-size: 52px; }

  /* front */
  .brand-panel {
    position: absolute; left: 0; top: 0; width: 380px; height: 100%;
    background: var(--brand-blue);
  }
  .details {
    position: absolute; right: 44px; top: 70px; text-align: right;
  }
  .holder-name {
    font-family: "Montserrat", sans-serif; font-weight: 700;
    font-size: 24px; color: var(--brand-blue-deep); letter-spacing: .5px;
  }
  .holder-role {
    font-family: "Roboto", sans-serif; font-size: 16px;
    color: var(--ink-soft); margin-top: 2px;
  }
  .contact-list { list-style: none; margin-top: 34px; }
  .contact-list li {
    display: flex; justify-content: flex-end; align-items: center; gap: 10px;
    font-family: "Roboto", sans-serif; font-size: 18px; color: var(--ink);
    line-height: 30px;
  }
  .contact-list svg { width: 18px; height: 18px; flex: none; }
  .front-wordmark {
    position: absolute; right: 44px; bottom: 70px;
    font-size: 34px; letter-spacing: 1px;
  }
</style>
</head>
<body>
<main class="canvas">
  <section class="card card--back" aria-label="Card back">
    <div class="back-brand">
      <span class="brand-dot" aria-hidden="true"></span>
      <span class="wordmark">TalkHarbor</span>
    </div>
  </section>

  <section class="card card--front" aria-label="Card front">
    <div class="brand-panel" role="img" aria-label="Large brand mark on blue field"></div>
    <div class="details">
      <p class="holder-name">ELLIS WARREN</p>
      <p class="holder-role">CEO/FOUNDER</p>
      <ul class="contact-list">
        <li>020 7946 0381
          <svg viewBox="0 0 18 18" aria-hidden="true"><rect x="4.5" y="1.5" width="9" height="15" rx="1.5" fill="none" stroke="#0a7ab8" stroke-width="1.6"/><circle cx="9" cy="13.5" r="1" fill="#0a7ab8"/></svg>
        </li>
        <li>Hello@talkharbor.co.uk
          <svg viewBox="0 0 18 18" aria-hidden="true"><rect x="1.5" y="4" width="15" height="10" fill="#0a7ab8"/><path d="M1.5 4 L9 10 L16.5 4" fill="none" stroke="#fff" stroke-width="1.3"/></svg>
        </li>
        <li>www.talkharbor.co.uk
          <svg viewBox="0 0 18 18" aria-hidden="true"><circle cx="9" cy="9" r="7.5" fill="#0a7ab8"/><ellipse cx="9" cy="9" rx="3.2" ry="7.5" fill="none" stroke="#fff" stroke-width="1"/><line x1="1.5" y1="9" x2="16.5" y2="9" stroke="#fff" stroke-width="1"/></svg>
        </li>
      </ul>
    </div>
    <p class="wordmark front-wordmark">TalkHarbor</p>
  </section>
</main>
</body>
</html>
```